Dalvick's Business Card

I need some designs for a new business card including the new logo attached. An old example of our business card is also attached to show all the data that should be included on the new design.
**I added some more examples someone had mocked up**

Contact Information for Business Card

Should include all info on other examples uploaded.

```html
<!DOCTYPE html>
<html lang="en">
<head>
<meta charset="utf-8">
<title>Dalvick's Business Card</title>
<link rel="stylesheet" href="https://fonts.googleapis.com/css2?family=Montserrat:wght@500;600;800&display=swap">
<style>
  :root {
    --brand-red: #e31e24;
    --brand-blue: #0a6ebd;
    --ink: #1c1c1c;
    --paper: #ffffff;
    --backdrop: #e9ebee;
  }
  * { box-sizing: border-box; margin: 0; padding: 0; }
  html, body { width: 1200px; height: 866px; overflow: hidden; }
  body {
    background: var(--backdrop);
    font-family: "Montserrat", Arial, sans-serif;
    display: flex; align-items: center; justify-content: center; gap: 30px;
  }
  .card {
    position: relative; width: 560px; height: 320px;
    background: var(--paper); overflow: hidden;
    box-shadow: 0 6px 18px rgba(0,0,0,.18);
  }
  .card svg.bands { position: absolute; inset: 0; }
  .brand { position: absolute; display: flex; align-items: center; gap: 10px; }
  .brand-dot { border-radius: 50%; background: var(--brand-blue); flex: none; }
  .brand-name { font-weight: 800; color: var(--brand-blue); letter-spacing: 1px; line-height: 1; }
  .brand-tagline { position: absolute; color: var(--brand-red); font-weight: 600; text-transform: uppercase; letter-spacing: .5px; white-space: nowrap; }

  /* front */
  .front .brand { left: 30px; top: 30px; }
  .front .brand-dot { width: 34px; height: 34px; }
  .front .brand-name { font-size: 34px; }
  .front .brand-tagline { left: 76px; top: 68px; font-size: 8px; }
  .owner { position: absolute; left: 30px; top: 106px; font-size: 20px; font-weight: 800; color: var(--brand-blue); letter-spacing: 1px; white-space: nowrap; }
  .rule { position: absolute; left: 30px; height: 1px; background: var(--brand-blue); }
  .contact { position: absolute; left: 30px; top: 150px; list-style: none; font-size: 15px; color: var(--ink); font-weight: 500; }
  .contact li { display: flex; align-items: center; gap: 8px; height: 24px; white-space: nowrap; }
  .contact svg { width: 14px; height: 14px; flex: none; }
  .band-text { position: absolute; color: #fff; font-weight: 800; text-transform: uppercase; letter-spacing: 1px; white-space: nowrap; }
  .front .licensed { left: 24px; top: 264px; font-size: 13px; }
  .front .family { left: 262px; top: 285px; font-size: 14px; }

  /* back */
  .back .brand { left: 0; right: 0; top: 46px; justify-content: center; }
  .back .brand-dot { width: 44px; height: 44px; }
  .back .brand-name { font-size: 48px; }
  .back .brand-tagline { left: 0; right: 0; top: 100px; text-align: center; font-size: 11px; }
  .back .served { left: 0; right: 0; top: 170px; text-align: center; font-size: 13px; font-weight: 600; text-transform: none; letter-spacing: .5px; transform: rotate(3deg); }
  .back .call { left: 0; right: 0; top: 232px; text-align: center; font-size: 16px; line-height: 1.35; white-space: normal; transform: rotate(3deg); }
</style>
</head>
<body>

<section class="card front">
  <svg class="bands" width="560" height="320" viewBox="0 0 560 320" aria-hidden="true">
    <polygon points="0,252 240,252 262,292 0,292" fill="var(--brand-red)"/>
    <polygon points="0,292 262,292 266,300 0,300" fill="var(--brand-blue)"/>
    <polygon points="230,276 560,276 560,320 250,320" fill="var(--brand-blue)"/>
    <polygon points="225,268 560,268 560,272 228,272" fill="var(--brand-blue)"/>
  </svg>
  <div class="brand"><span class="brand-dot"></span><span class="brand-name">DALVICK'S</span></div>
  <p class="brand-tagline">Air Conditioning &amp; Heating Service</p>
  <h1 class="owner">MARCUS DALVICK</h1>
  <div class="rule" style="top:138px;width:230px"></div>
  <ul class="contact">
    <li><svg viewBox="0 0 24 24"><path fill="var(--brand-red)" d="M6.6 10.8a15 15 0 0 0 6.6 6.6l2.2-2.2c.3-.3.7-.4 1-.2 1.1.4 2.3.6 3.6.6.6 0 1 .4 1 1V20c0 .6-.4 1-1 1A17 17 0 0 1 3 4c0-.6.4-1 1-1h3.5c.6 0 1 .4 1 1 0 1.3.2 2.5.6 3.6.1.3 0 .7-.2 1z"/></svg>555.014.7730</li>
    <li><svg viewBox="0 0 24 24"><rect x="2" y="5" width="20" height="14" fill="var(--brand-red)"/><path d="M2 5l10 8 10-8" fill="none" stroke="#fff" stroke-width="2"/></svg>hvacdalvick@mailbox.com</li>
  </ul>
  <div class="rule" style="top:208px;width:300px"></div>
  <p class="band-text licensed">Licensed &amp; Insured</p>
  <p class="band-text family">Family Owned &amp; Operated</p>
</section>

<section class="card back">
  <svg class="bands" width="560" height="320" viewBox="0 0 560 320" aria-hidden="true">
    <polygon points="0,150 560,180 560,212 0,182" fill="var(--brand-red)"/>
    <polygon points="0,182 560,212 560,320 0,320" fill="var(--brand-blue)"/>
  </svg>
  <div class="brand"><span class="brand-dot"></span><span class="brand-name">DALVICK'S</span></div>
  <p class="brand-tagline">Air Conditioning &amp; Heating Service</p>
  <p class="band-text served">Serves Brookfield, IA &amp; Surrounding Areas</p>
  <p class="band-text call">Call today for all your HVAC,<br>Refrigeration &amp; Plumbing needs</p>
</section>

</body>
</html>
```